Plumbing company needs Business Card Design

Hi I need business card design based on logo which I uploaded. Its plumbing and heating company called Kranex Usługi Hydrauliczno-Gazowe. I want to see on my card motto of my company which is "...od cieknącego kranu po nową łazienkę.", my phone number, name, and website: 612478390, Marek Olejnik, info@kranex-inst.org, www.kranex-inst.org
I want to see logos of companys which I'm approved installer (Termova) (Le Valmont) (Korvo) (Plumox).
I want new creative look of business card. I like rounded corners.
Any questions please send message.
Thanks for intrest.
Industry/Entity Type
Business
Contact Information for Business Card
Marek Olejnik
612 478 390
info@kranex-inst.org
www.kranex-inst.org
...od cieknącego kranu po nową łazienkę.

```html
<!DOCTYPE html>
<html lang="pl">
<head>
<meta charset="utf-8">
<title>Kranex – wizytówka</title>
<link rel="stylesheet" href="https://fonts.googleapis.com/css2?family=Ubuntu:wght@500;700&family=Oswald:wght@400;500&family=Open+Sans:wght@400;600&display=swap">
<style>
  :root {
    --navy: #1f3f8c;
    --red: #e1261c;
    --yellow: #ffe81a;
    --paper: #f7f7f5;
    --ink: #333;
    --stage: #ece8e0;
    --white: #fff;
  }
  * { box-sizing: border-box; margin: 0; padding: 0; }
  html, body { width: 1200px; height: 840px; overflow: hidden; }
  body {
    background: var(--stage);
    display: flex; align-items: center; justify-content: center; gap: 80px;
    font-family: "Open Sans", Arial, sans-serif;
  }
  .card {
    width: 440px; height: 440px; border-radius: 30px;
    position: relative; overflow: hidden;
    box-shadow: 0 6px 18px rgba(0,0,0,.18);
  }
  /* Front */
  .card--front { background: var(--paper); }
  .brand { position: absolute; left: 30px; top: 30px; display: flex; align-items: center; gap: 14px; }
  .brand__mark {
    width: 112px; height: 96px; border-radius: 16px;
    background: var(--yellow); flex: none;
  }
  .brand__text { display: flex; flex-direction: column; }
  .brand__name {
    font-family: "Ubuntu", sans-serif; font-weight: 700;
    font-size: 52px; line-height: 1; color: var(--red);
  }
  .brand__tagline {
    font-family: "Oswald", sans-serif; font-weight: 500;
    font-size: 18px; color: var(--navy); margin-top: 4px; white-space: nowrap;
  }
  .holder {
    position: absolute; left: 44px; top: 158px;
    font-family: "Ubuntu", sans-serif; font-weight: 700;
    font-size: 25px; letter-spacing: 1px; color: var(--navy);
  }
  .contacts { position: absolute; left: 44px; top: 208px; list-style: none; }
  .contacts li {
    display: flex; align-items: center; gap: 14px;
    font-size: 19px; color: var(--ink); height: 30px; margin-bottom: 2px;
  }
  .contacts .icon {
    width: 22px; height: 22px; border-radius: 5px; background: var(--red);
    display: flex; align-items: center; justify-content: center; flex: none;
  }
  .footer-band {
    position: absolute; left: 0; right: 0; bottom: 0; height: 118px;
    background: var(--navy);
    border-top: 5px solid var(--red);
    box-shadow: 0 -6px 0 var(--paper), 0 -8px 0 var(--red);
    display: flex; align-items: center; padding: 0 24px;
  }
  .motto { color: var(--white); font-size: 17px; font-weight: 600; line-height: 1.5; }
  /* Back */
  .card--back {
    background: var(--navy);
    display: flex; align-items: center; justify-content: center;
  }
  .card--back .brand { position: static; flex-direction: column; gap: 16px; }
  .card--back .brand__mark { width: 136px; height: 116px; }
  .card--back .brand__text { align-items: center; }
  .card--back .brand__name { font-size: 64px; }
  .card--back .brand__tagline { color: var(--white); font-size: 22px; }
</style>
</head>
<body>
  <section class="card card--front" aria-label="Przód wizytówki">
    <div class="brand">
      <div class="brand__mark"></div>
      <div class="brand__text">
        <span class="brand__name">Kranex</span>
        <span class="brand__tagline">Usługi Hydrauliczno-Gazowe</span>
      </div>
    </div>
    <h1 class="holder">MAREK OLEJNIK</h1>
    <ul class="contacts">
      <li><span class="icon"><svg width="13" height="13" viewBox="0 0 24 24"><path fill="#fff" d="M6.6 10.8a15 15 0 0 0 6.6 6.6l2.2-2.2c.3-.3.7-.4 1-.2 1.1.4 2.3.6 3.6.6.6 0 1 .4 1 1V20c0 .6-.4 1-1 1A17 17 0 0 1 3 4c0-.6.4-1 1-1h3.5c.6 0 1 .4 1 1 0 1.3.2 2.5.6 3.6.1.3 0 .7-.2 1z"/></svg></span>612478390</li>
      <li><span class="icon"><svg width="14" height="12" viewBox="0 0 24 18"><rect x="1" y="1" width="22" height="16" rx="2" fill="none" stroke="#fff" stroke-width="2"/><path d="M1 2l11 8 11-8" fill="none" stroke="#fff" stroke-width="2"/></svg></span>info@kranex-inst.org</li>
      <li><span class="icon"><svg width="14" height="14" viewBox="0 0 24 24" fill="none" stroke="#fff" stroke-width="2"><circle cx="12" cy="12" r="10"/><ellipse cx="12" cy="12" rx="4" ry="10"/><path d="M2 12h20M4 6h16M4 18h16"/></svg></span>www.kranex-inst.org</li>
    </ul>
    <div class="footer-band">
      <p class="motto">...od cieknącego kranu po nową łazienkę</p>
    </div>
  </section>

  <section class="card card--back" aria-label="Tył wizytówki">
    <div class="brand">
      <div class="brand__mark"></div>
      <div class="brand__text">
        <span class="brand__name">Kranex</span>
        <span class="brand__tagline">Usługi Hydrauliczno-Gazowe</span>
      </div>
    </div>
  </section>
</body>
</html>
```